LumaVerge New Website

LumaVerge is a digital marketing agency. Our clients are all limousine companies. We need a responsive website designed to highlight our services and products. Our competition is http://www.cobaltreachpartners.example/ and we need a site of similar design and layout without being too similar. Our old website www.lumaverge.example, is very outdated and the logo and graphics have changed. We will adjust the content to work with the new design. The new logo is attached.

```html
<!DOCTYPE html>
<html lang="en">
<head>
<meta charset="utf-8">
<title>LumaVerge — Digital Marketing for Limousine Companies</title>
<link href="https://fonts.googleapis.com/css2?family=Lato:ital,wght@0,300;0,400;0,700;0,900;1,700;1,900&family=Sorts+Mill+Goudy&display=swap" rel="stylesheet">
<style>
  :root{
    --navy:#1a4b64;
    --gold:#b8a252;
    --gold-ring:#bda65a;
    --ink:#2c3b45;
    --muted:#7d8a93;
    --line:#bfc3c6;
    --panel:#f4f5f7;
    --card-label:#eef0f2;
    --footer:#e9e9e9;
    --white:#ffffff;
  }
  *{box-sizing:border-box;margin:0;padding:0}
  html,body{width:700px;height:1200px;overflow:hidden;background:var(--white)}
  body{font-family:"Lato",Arial,sans-serif;color:var(--ink)}
  .page{position:relative;width:700px;height:1200px;overflow:hidden}
  .abs{position:absolute}

  /* top bar */
  .topbar{left:0;top:0;width:700px;height:25px;background:var(--navy);color:var(--white)}
  .lang{left:58px;top:7px;font-size:7.5px;font-weight:700}
  .social-top{right:58px;top:8px;display:flex;gap:6px}
  .social-top span{width:8px;height:8px;border-radius:50%;background:rgba(255,255,255,.85)}

  /* header */
  .header{left:0;top:25px;width:700px;height:51px;background:var(--white)}
  .wordmark{display:flex;align-items:center;gap:6px;font-size:21px;font-weight:700;color:var(--navy);line-height:1}
  .wordmark .dot{width:12px;height:12px;border-radius:50%;background:var(--navy)}
  .brand{left:68px;top:11px}
  .brand-tag{left:86px;top:38px;font-size:5px;font-weight:700;color:var(--navy);letter-spacing:.4px}
  .nav{left:257px;top:17px;display:flex;gap:11px;font-size:7.6px;font-weight:700;color:var(--navy)}
  .search{left:632px;top:16px}

  /* hero */
  .hero{left:0;top:76px;width:700px;height:254px;background:linear-gradient(90deg,#eef1f2 0%,#e3e8ea 45%,#dfe6e8 75%,#e9eef0 100%)}
  .hero-visual{left:48px;top:84px;width:196px;height:246px;background:radial-gradient(ellipse at 55% 35%,#8fc255 0%,#6ea33c 28%,#e5c6b3 55%,rgba(230,215,205,0) 78%)}
  .hero-title{left:313px;top:103px;font-family:"Sorts Mill Goudy",Georgia,serif;font-size:20px;font-weight:400;line-height:30px;color:var(--navy)}
  .contact-card{top:176px;width:94px;height:94px;background:var(--white);text-align:center;color:var(--navy)}
  .contact-card svg{margin-top:18px}
  .contact-card .label{font-size:11px;margin-top:6px;line-height:15px}
  .contact-card .value{font-size:11px}
  .contact-card .value.small{font-size:7.8px}
  .cta{left:521px;top:291px;width:100px;height:21px;background:var(--gold);color:var(--white);font-size:10px;text-align:center;line-height:21px;border-radius:2px}

  /* timeline */
  .timeline{left:0;top:330px;width:700px;height:190px}
  .tl-label{position:absolute;font-size:8.2px;color:var(--navy);text-align:center;width:110px;line-height:11px}

  /* overview */
  .overview{left:0;top:520px;width:700px;height:222px;background:var(--panel);border-top:1px solid #e6e8ea;border-bottom:1px solid #e6e8ea}
  .slogan{left:0;top:12px;width:700px;text-align:center;font-size:17px;font-weight:900;font-style:italic;color:var(--navy)}
  .overview-photo{left:57px;top:61px;width:285px;height:145px;background:linear-gradient(120deg,#f1eef3 0%,#e6e2ea 50%,#d9d3de 100%)}
  .overview-title{left:357px;top:59px;font-size:15px;font-weight:900;letter-spacing:2.2px;color:var(--navy)}
  .overview-text{left:357px;top:86px;width:288px;font-size:6.4px;line-height:11.5px;color:#3b4750}
  .overview-text p+p{margin-top:7px}
  .view-more{left:357px;top:169px;width:84px;height:24px;border:1px solid #cfd4d8;background:var(--white);font-size:7.6px;font-weight:900;color:var(--navy);text-align:center;line-height:22px}

  /* team */
  .team-title{left:0;top:760px;width:700px;text-align:center;font-size:17px;font-weight:700;font-style:italic;color:var(--ink)}
  .team-sub{left:0;top:786px;width:700px;text-align:center;font-size:6px;color:#a0aab1}
  .member{top:808px;width:146px;height:159px;border:1px solid #d3dde3}
  .member .photo{height:109px}
  .member .info{height:49px;background:var(--card-label);padding:10px 14px;color:var(--ink)}
  .member .name{font-size:9px;font-weight:700}
  .member .role{font-size:7.3px;margin-top:4px}
  .member.active .info{background:var(--navy);color:var(--white)}
  .arrow{top:875px;width:24px;height:24px;border-radius:50%}

  /* footer */
  .footer{left:0;top:998px;width:700px;height:168px;background:var(--footer)}
  .f-brand{left:74px;top:30px}
  .f-tag{left:92px;top:57px;font-size:5px;font-weight:700;color:var(--navy);letter-spacing:.4px}
  .f-contact{left:78px;top:73px;font-size:7px;line-height:8.5px;color:#333}
  .f-contact .row{display:flex;gap:7px;margin-bottom:6px}
  .f-col-title{font-size:9.5px;font-weight:700;color:#2d2d2d}
  .f-links{list-style:none;font-size:7px;color:#333}
  .f-links li{margin-top:9.5px}
  .f-links li::before{content:"»";margin-right:6px}
  .divider{top:22px;width:2px;height:120px;background:linear-gradient(180deg,rgba(0,0,0,0),rgba(0,0,0,.08),rgba(0,0,0,0))}
  .news-text{font-size:6.8px;line-height:11px;color:#444;text-align:center;width:116px}
  .email-field{width:119px;height:21px;border:1px solid #9aa3a8;border-radius:6px;background:var(--white);font-size:7px;font-style:italic;color:#8a959b;padding:5px 7px}
  .subscribe{width:63px;height:18px;background:var(--navy);color:var(--white);font-size:7.5px;font-weight:900;font-style:italic;text-align:center;line-height:18px;border-radius:2px}
  .follow{display:flex;align-items:center;gap:11px;font-size:8.8px;color:#222;margin-top:5px}
  .follow .box{width:22px;height:23px;border:1px solid #222;border-radius:3px;background:var(--white)}
  .copyright{left:0;top:1166px;width:700px;height:34px;background:var(--navy);color:var(--white);font-size:8.5px;font-weight:700;text-align:center;line-height:34px}
</style>
</head>
<body>
<div class="page">

  <div class="abs topbar">
    <div class="abs lang">Choose Your Languages &#9662;</div>
    <div class="abs social-top"><span></span><span></span><span></span><span></span><span></span><span></span><span></span><span></span></div>
  </div>

  <header class="abs header">
    <div class="abs brand wordmark"><span class="dot"></span>LumaVerge</div>
    <div class="abs brand-tag">LIMOUSINE MARKETING PARTNERS</div>
    <nav class="abs nav">
      <span>Home</span><span>Integrated Marketing</span><span>Services</span><span>News &amp; Events</span><span>RouteRewards™</span><span>Blog</span><span>Contact Us</span>
    </nav>
    <svg class="abs search" width="12" height="12" viewBox="0 0 12 12"><circle cx="7" cy="5" r="3.6" fill="none" stroke="#1a4b64" stroke-width="1"/><line x1="4.4" y1="7.6" x2="1.5" y2="10.5" stroke="#1a4b64" stroke-width="1"/></svg>
  </header>

  <section class="abs hero" role="img" aria-label="Softly blurred bright office backdrop"></section>
  <div class="abs hero-visual" role="img" aria-label="Hand holding a light bulb growing green leaves"></div>
  <h1 class="abs hero-title">We Have A Passion For What We Do.<br>Let Us Do What We Do Best .</h1>

  <div class="abs contact-card" style="left:317px">
    <svg width="10" height="14" viewBox="0 0 10 14"><rect x="1" y="1" width="8" height="12" rx="1.5" fill="none" stroke="#b8a252" stroke-width="1.2"/><circle cx="5" cy="10.5" r=".8" fill="#b8a252"/></svg>
    <div class="label">Toll Free:</div>
    <div class="value">855-555-0147</div>
  </div>
  <div class="abs contact-card" style="left:425px">
    <svg width="18" height="15" viewBox="0 0 18 15"><rect x="1" y="3" width="11" height="11" rx="1" fill="none" stroke="#b8a252" stroke-width="1.3"/><path d="M7 9 L15 1 L17 3 L9 11 L6.5 11.5 Z" fill="none" stroke="#b8a252" stroke-width="1.3"/></svg>
    <div class="label">E-mail:</div>
    <div class="value small">info@lumaverge.example</div>
  </div>
  <div class="abs contact-card" style="left:533px">
    <svg width="16" height="16" viewBox="0 0 16 16"><path d="M3 1 L6 1 L7 5 L5 6.5 C6 9 7.5 10.5 9.5 11.5 L11 9.5 L15 10.5 L15 13.5 C9 15 1 7 3 1 Z" fill="#b8a252"/></svg>
    <div class="label">Click To<br>Call</div>
  </div>
  <div class="abs cta">Get Started Now</div>

  <section class="abs timeline">
    <svg width="700" height="190" viewBox="0 0 700 190">
      <line x1="50" y1="96" x2="652" y2="96" stroke="#bfc3c6" stroke-width="3"/>
      <path d="M47 96 L54 92 L54 100 Z M655 96 L648 92 L648 100 Z" fill="#bfc3c6"/>
      <g stroke="#bfc3c6" stroke-width="3">
        <line x1="106" y1="75" x2="106" y2="86"/><line x1="204" y1="106" x2="204" y2="118"/>
        <line x1="303" y1="75" x2="303" y2="86"/><line x1="398" y1="106" x2="398" y2="118"/>
        <line x1="491" y1="75" x2="491" y2="86"/><line x1="587" y1="106" x2="587" y2="118"/>
      </g>
      <g fill="#fff" stroke="#bda65a" stroke-width="5">
        <circle cx="106" cy="96" r="8"/><circle cx="204" cy="96" r="8"/><circle cx="303" cy="96" r="8"/>
        <circle cx="398" cy="96" r="8"/><circle cx="491" cy="96" r="8"/><circle cx="587" cy="96" r="8"/>
      </g>
      <g fill="#1a4b64">
        <circle cx="106" cy="49" r="25.5"/><circle cx="303" cy="49" r="25.5"/><circle cx="491" cy="49" r="25.5"/>
        <circle cx="204" cy="143" r="25.5"/><circle cx="398" cy="143" r="25.5"/><circle cx="587" cy="143" r="25.5"/>
      </g>
      <rect x="98" y="42" width="16" height="13" fill="none" stroke="#fff" stroke-width="1.5"/>
      <g fill="#fff"><rect x="101" y="48" width="2" height="5"/><rect x="104.5" y="45" width="2" height="8"/><rect x="108" y="47" width="2" height="6"/></g>
      <g fill="#fff"><circle cx="303" cy="44" r="3.5"/><circle cx="296" cy="46" r="2.7"/><circle cx="310" cy="46" r="2.7"/>
        <path d="M296 56 Q303 46 310 56 Z"/><path d="M290 55 Q296 48 300 53 L299 55Z"/><path d="M316 55 Q310 48 306 53 L307 55Z"/></g>
      <rect x="483" y="42" width="16" height="13" fill="none" stroke="#fff" stroke-width="1.5"/>
      <path d="M485 53 L489 48 L492 51 L494 49 L497 53 Z" fill="#fff"/><circle cx="494" cy="45.5" r="1.2" fill="#fff"/>
      <g fill="none" stroke="#fff" stroke-width="1.8" stroke-linecap="round">
        <path d="M199 139 L204 135 L209 139"/><path d="M211 143 L209 149 L203 149"/><path d="M197 143 L198 149 L201 149"/>
      </g>
      <rect x="394" y="136" width="8" height="13" rx="1.2" fill="none" stroke="#fff" stroke-width="1.4"/><circle cx="398" cy="146.5" r=".8" fill="#fff"/>
      <g fill="#fff"><circle cx="587" cy="135" r="1.5"/><circle cx="593" cy="139" r="1.4"/><circle cx="594" cy="145" r="1.3"/><circle cx="589" cy="150" r="1.2"/><circle cx="583" cy="149" r="1.1"/><circle cx="580" cy="143" r="1"/><circle cx="582" cy="137" r=".9"/></g>
    </svg>
    <div class="tl-label" style="left:52px;top:119px">Inbound Marketing</div>
    <div class="tl-label" style="left:153px;top:62px">Outbound Marketing</div>
    <div class="tl-label" style="left:249px;top:119px">Social Media Marketing</div>
    <div class="tl-label" style="left:343px;top:62px">Mobile marketing</div>
    <div class="tl-label" style="left:436px;top:119px">Online Image &amp;<br>Reputation Management</div>
    <div class="tl-label" style="left:532px;top:51px">Support To Complete the<br>Sale</div>
  </section>

  <section class="abs overview">
    <h2 class="abs slogan">We're Not Just Raising the Stakes. We're Changing the Game.</h2>
    <div class="abs overview-photo" role="img" aria-label="Businessman sketching growth charts on a whiteboard"></div>
    <h3 class="abs overview-title">LUMAVERGE OVERVIEW</h3>
    <div class="abs overview-text">
      <p>Lorem ipsum dolor sit amet, consectetur adipiscing elit. Duis ut lobortis nulla. Vestibulum ante ipsum primis in faucibus orci luctus et ultrices posuere cubilia.</p>
      <p>Phasellus ut condimentum diam, eget tempus lorem. Morbi bibendum est quis arcu posuere condimentum. Nullam justo eros, pellentesque a metus non, mattis volutpat libero. Praesent ornare felis ante, sit amet porta felis pellentesque fermentum.</p>
    </div>
    <div class="abs view-more">VIEW MORE &#8250;</div>
  </section>

  <h2 class="abs team-title">Our Team</h2>
  <div class="abs team-sub">Our design is coupled with the excellent value</div>

  <div class="abs member" style="left:58px">
    <div class="photo" role="img" aria-label="Portrait of a team member" style="background:linear-gradient(180deg,#fff 0%,#f3ece8 60%,#d9c7bd 100%)"></div>
    <div class="info"><div class="name">Person Name</div><div class="role">Designation</div></div>
  </div>
  <div class="abs member" style="left:204px">
    <div class="photo" role="img" aria-label="Portrait of a team member" style="background:linear-gradient(180deg,#fff 0%,#efe9e5 55%,#5b5d62 100%)"></div>
    <div class="info"><div class="name">Person Name</div><div class="role">Designation</div></div>
  </div>
  <div class="abs member active" style="left:350px">
    <div class="photo" role="img" aria-label="Portrait of a team member" style="background:linear-gradient(180deg,#fff 0%,#f2e6dc 55%,#b59a86 100%)"></div>
    <div class="info"><div class="name">Person Name</div><div class="role">Designation</div></div>
  </div>
  <div class="abs member" style="left:496px">
    <div class="photo" role="img" aria-label="Portrait of a team member" style="background:linear-gradient(180deg,#fff 0%,#ede3dc 55%,#6d9ac7 100%)"></div>
    <div class="info"><div class="name">Person Name</div><div class="role">Designation</div></div>
  </div>

  <svg class="abs arrow" style="left:12px" viewBox="0 0 24 24"><circle cx="12" cy="12" r="12" fill="#cfd3d6"/><path d="M14 7 L9 12 L14 17" fill="none" stroke="#fff" stroke-width="1.6"/></svg>
  <svg class="abs arrow" style="left:664px" viewBox="0 0 24 24"><circle cx="12" cy="12" r="12" fill="#1a4b64"/><path d="M10 7 L15 12 L10 17" fill="none" stroke="#fff" stroke-width="1.6"/></svg>

  <footer class="abs footer">
    <div class="abs f-brand wordmark"><span class="dot"></span>LumaVerge</div>
    <div class="abs f-tag">LIMOUSINE MARKETING PARTNERS</div>
    <div class="abs f-contact">
      <div class="row">
        <svg width="6" height="9" viewBox="0 0 6 9"><path d="M3 9 L0.6 4 A2.7 2.7 0 1 1 5.4 4 Z" fill="#333"/><circle cx="3" cy="3" r="1" fill="#e9e9e9"/></svg>
        <span>210 Harbor Street,<br>8th Floor, Boston,<br>MA 02110-1204,<br>United States</span>
      </div>
      <div class="row" style="margin-top:4px">
        <svg width="7" height="7" viewBox="0 0 16 16"><path d="M3 1 L6 1 L7 5 L5 6.5 C6 9 7.5 10.5 9.5 11.5 L11 9.5 L15 10.5 L15 13.5 C9 15 1 7 3 1 Z" fill="#333"/></svg>
        <span>855-555-0147</span>
      </div>
      <div class="row" style="margin-top:4px">
        <svg width="8" height="6" viewBox="0 0 8 6"><rect width="8" height="6" fill="#333"/><path d="M0 0 L4 3 L8 0" fill="none" stroke="#e9e9e9" stroke-width=".7"/></svg>
        <span>info@lumaverge.example</span>
      </div>
    </div>

    <div class="abs divider" style="left:206px"></div>
    <div class="abs" style="left:220px;top:20px">
      <div class="f-col-title">Quick links</div>
      <ul class="f-links">
        <li>Integrated Marketing</li><li>Services</li><li>News &amp; Events</li><li>RouteRewards™</li><li>Blog</li><li>Contact Us</li>
      </ul>
    </div>

    <div class="abs divider" style="left:348px"></div>
    <div class="abs" style="left:359px;top:20px">
      <div class="f-col-title">Newslatter Singup</div>
      <p class="news-text" style="margin-top:9px;margin-left:5px">Our email newsletters are a great way to get the information you're looking for at lumaverge.example</p>
      <div class="email-field" style="margin-top:9px">Email Id</div>
      <div class="subscribe" style="margin-top:12px;margin-left:29px">SUBSCRIBE</div>
    </div>

    <div class="abs divider" style="left:493px"></div>
    <div class="abs" style="left:514px;top:20px">
      <div class="f-col-title">Stay Connected</div>
      <div style="margin-top:4px;margin-left:13px">
        <div class="follow"><span class="box"></span>Social Feed</div>
        <div class="follow"><span class="box"></span>Short Posts</div>
        <div class="follow"><span class="box"></span>Pro Network</div>
        <div class="follow"><span class="box"></span>Circles</div>
      </div>
    </div>
  </footer>

  <div class="abs copyright">Copyright © 2014 LumaVerge</div>
</div>
</body>
</html>
```